furniture and home contents restoration

I need to list the services that we perform in our studio.
we serve the general public as well as the insurance/ remediation industry

```html
<!DOCTYPE html>
<html lang="en">
<head>
<meta charset="utf-8">
<title>Northgate Refinishers – Business Card</title>
<link href="https://fonts.googleapis.com/css2?family=Libre+Baskerville:wght@400;700&family=PT+Serif:wght@400;700&display=swap" rel="stylesheet">
<style>
  :root {
    --page-bg: #d3cfc9;
    --card-bg: #1f323b;
    --ink: #ffffff;
    --ink-soft: #e6ecee;
  }
  * { box-sizing: border-box; margin: 0; padding: 0; }
  html, body { width: 1200px; height: 930px; overflow: hidden; }
  body {
    background: var(--page-bg);
    display: flex;
    flex-direction: column;
    align-items: center;
    justify-content: center;
    gap: 40px;
    font-family: "PT Serif", Georgia, serif;
    color: var(--ink);
  }
  .card {
    position: relative;
    width: 700px;
    height: 400px;
    background: var(--card-bg);
    border-radius: 18px;
    box-shadow: 0 6px 18px rgba(0,0,0,0.18);
    overflow: hidden;
  }

  /* Back side: services */
  .services-title {
    position: absolute;
    top: 32px; left: 0; right: 0;
    text-align: center;
    font-family: "Libre Baskerville", Georgia, serif;
    font-weight: 700;
    font-size: 30px;
    letter-spacing: 0.5px;
  }
  .service-columns {
    position: absolute;
    top: 92px; left: 40px; right: 30px;
    display: grid;
    grid-template-columns: 1fr 1.08fr;
    column-gap: 20px;
  }
  .service-list {
    list-style: none;
    font-size: 11.5px;
    line-height: 19px;
    text-transform: uppercase;
    letter-spacing: 0.2px;
    white-space: nowrap;
  }
  .service-list li::before {
    content: "•";
    margin-right: 6px;
  }
  .assessment-lines {
    position: absolute;
    right: 40px; bottom: 32px;
    text-align: right;
    font-size: 15px;
    line-height: 22px;
    text-transform: uppercase;
    letter-spacing: 0.2px;
    white-space: nowrap;
  }

  /* Front side: contact */
  .brand-name {
    position: absolute;
    top: 62px; left: 44px;
    font-family: "Libre Baskerville", Georgia, serif;
    font-weight: 700;
    font-size: 34px;
    line-height: 40px;
    letter-spacing: 0.5px;
  }
  .brand-name .line-two { display: block; padding-left: 30px; }
  .tagline {
    position: absolute;
    top: 40px; left: 400px; right: 30px;
    font-size: 15px;
    line-height: 18px;
    color: var(--ink-soft);
  }
  .tagline .line-two { display: block; padding-left: 14px; }
  .contact-block {
    position: absolute;
    top: 206px; left: 404px; right: 20px;
    font-size: 14px;
    line-height: 19px;
    list-style: none;
    white-space: nowrap;
  }
  .contact-block li { display: flex; align-items: center; gap: 7px; }
  .contact-block svg { width: 11px; height: 11px; flex: none; fill: var(--ink); }
  .specialty {
    position: absolute;
    top: 316px; left: 414px;
    font-size: 15px;
    text-transform: uppercase;
    letter-spacing: 0.3px;
    white-space: nowrap;
  }
  .person-name {
    position: absolute;
    left: 44px; bottom: 40px;
    display: flex; align-items: center; gap: 16px;
    font-family: "Libre Baskerville", Georgia, serif;
    font-weight: 700;
    font-size: 27px;
    letter-spacing: 0.5px;
  }
  .person-name .marker {
    width: 22px; height: 22px;
    background: var(--ink);
  }
</style>
</head>
<body>

<section class="card card--services" aria-label="Services side">
  <h2 class="services-title">NORTHGATE REFINISHERS</h2>
  <div class="service-columns">
    <ul class="service-list">
      <li>Antique repair and restoration</li>
      <li>Art cleaning and remounting</li>
      <li>Art and mirror frame repair</li>
      <li>Chandelier cleaning and restoration</li>
      <li>Document restoration</li>
      <li>Glass, ceramic, and mirror repair</li>
      <li>Hardware repair and restoration</li>
      <li>Kitchen removal and reinstallation</li>
      <li>Lamp cleaning and restoration</li>
      <li>Lamp shade replacement</li>
    </ul>
    <ul class="service-list">
      <li>Metal polishing and restoration</li>
      <li>Odor removal and ozone services</li>
      <li>Photo restoration</li>
      <li>Upholstery cleaning and deodorizing</li>
      <li>In-house upholstery and reupholstery</li>
      <li>Rug cleaning and restoration</li>
      <li>Musical instrument restoration</li>
      <li>Window treatment repair/ restoration</li>
      <li>Leather restoration and replacement</li>
      <li>Piano restoration and repair</li>
    </ul>
  </div>
  <p class="assessment-lines">
    On-site inspections and desk review services<br>
    Assessment reports and estimates for repair and restoration
  </p>
</section>

<section class="card card--contact" aria-label="Contact side">
  <h1 class="brand-name">NORTHGATE<span class="line-two">REFINISHERS</span></h1>
  <p class="tagline">serving the general public and the<span class="line-two">insurance industry for over 40 years</span></p>

  <ul class="contact-block">
    <li>
      <svg viewBox="0 0 12 12" aria-hidden="true"><path d="M2.4 0.6 L4.2 2.6 L3.2 4 Q4.3 6.6 8 8.8 L9.4 7.8 L11.4 9.6 L10 11.4 Q4.6 11 0.6 2 Z"/></svg>
      914 555 0142
    </li>
    <li>
      <svg viewBox="0 0 12 12" aria-hidden="true"><path d="M3 0 H9 V12 H3 Z M4 1.5 V9 H8 V1.5 Z M5.5 10 H6.5 V11 H5.5 Z" fill-rule="evenodd"/></svg>
      914 555 0187
    </li>
    <li>
      <svg viewBox="0 0 12 12" aria-hidden="true"><path d="M3 0 H9 V4 H11 V10 H1 V4 H3 Z M4 1 V4 H8 V1 Z M3 6 V7 H9 V6 Z" fill-rule="evenodd"/></svg>
      914 555 0163
    </li>
    <li>
      <svg viewBox="0 0 12 12" aria-hidden="true"><path d="M6 0 A4 4 0 0 1 10 4 C10 7 6 12 6 12 C6 12 2 7 2 4 A4 4 0 0 1 6 0 Z M6 2.5 A1.5 1.5 0 1 0 6 5.5 A1.5 1.5 0 1 0 6 2.5 Z" fill-rule="evenodd"/></svg>
      18 birch hollow rd. larchmont, ny 10538
    </li>
    <li>
      <svg viewBox="0 0 12 12" aria-hidden="true"><path d="M0.5 2 H11.5 V10 H0.5 Z M1.6 3 L6 6.4 L10.4 3 Z M1.5 4.2 V9 H10.5 V4.2 L6 7.6 Z" fill-rule="evenodd"/></svg>
      northgate.studio@example.com
    </li>
  </ul>
  <p class="specialty">Home contents restoration</p>

  <p class="person-name"><span class="marker" aria-hidden="true"></span>DANIEL MORETTI</p>
</section>

</body>
</html>
```